Recruitment Site Design

We need a design for the login page, about page, and inner pages of a recruitment site for an oil and gas company. Design should be modern, sleek, professional and colors can be blue, green, white, orange or any other recommended colors.

Please also take into consideration that once the users login, they will need to access a form to fill in their information.

** UPDATE: Kindly provide a design for the inner information page consistent with the outer design. Attached is a picture of the basic structure. ***
Updates

Please provide a design for inner pages as shown in the design brief consistent with the registration page provided. 

Reason: We're extending it to get more inside pages.

Target Market(s)

Professionals looking for a career in the oil and gas industry in the Middle East.

Industry/Entity Type

Oil And Gas

Requirements
Must have
• Sleek design

```html
<!DOCTYPE html>
<html lang="en">
<head>
<meta charset="utf-8">
<title>Recruitment Home</title>
<link href="https://fonts.googleapis.com/css2?family=Signika:wght@400;500&display=swap" rel="stylesheet">
<style>
:root{
  --page:#f3f1f0;
  --band:#f6f5f5;
  --orange:#e8890e;
  --orange-light:#f9b544;
  --orange-dark:#d9750a;
  --text:#555;
  --nav-text:#444;
  --line:#dddbd9;
  --card:#f4f3f3;
  --footer-top:#5a5a5a;
  --footer-bottom:#323232;
}
*{margin:0;padding:0;box-sizing:border-box}
html,body{width:976px;height:1200px;overflow:hidden}
body{position:relative;background:var(--page);font-family:"Signika",sans-serif;color:var(--text)}
.abs{position:absolute}
.logo{left:0;width:976px;top:40px;text-align:center;font-size:58px;color:var(--orange);line-height:1}
.nav{left:114px;top:118px;width:748px;height:45px;display:flex;background:linear-gradient(#f3f2f2,#e7e5e4);box-shadow:0 2px 3px rgba(0,0,0,.12)}
.nav a{display:flex;align-items:center;justify-content:center;text-decoration:none;color:var(--nav-text);font-size:13.5px;border-right:1px solid #d6d4d2}
.nav a:last-child{border-right:0}
.nav a.active{color:var(--orange)}
.slider-band{left:0;top:165px;width:976px;height:321px;background:var(--band);border-top:2px solid var(--line);border-bottom:2px solid var(--line)}
.slide-shadow{left:215px;top:430px;width:546px;height:24px;border-radius:50%;background:radial-gradient(ellipse at center,rgba(0,0,0,.14),rgba(0,0,0,0) 70%)}
.slide-frame{left:178px;top:187px;width:621px;height:253px;background:#fff;box-shadow:0 1px 3px rgba(0,0,0,.1)}
.slide-photo{left:8px;top:11px;width:604px;height:235px;background:linear-gradient(90deg,#b8c2cf,#eef1f4 40%,#dfe4ea 70%,#aab7c8)}
.dots{left:484px;top:463px;display:flex;gap:2px}
.dots span{width:5px;height:5px;border-radius:50%;background:#666}
.card{top:518px;width:201px;height:239px;background:linear-gradient(#fff 0,#fff 20px,var(--card) 20px,#ebeaea);box-shadow:0 4px 5px rgba(0,0,0,.18)}
.card-head{left:-9px;top:20px;width:219px;height:36px;background:linear-gradient(var(--orange-light),var(--orange));color:#fff;font-size:20px;text-align:center;line-height:36px;letter-spacing:.5px;box-shadow:0 2px 2px rgba(0,0,0,.2)}
.card-text{position:absolute;left:17px;top:64px;width:167px;font-size:13px;line-height:20.3px}
.card-text span{display:block;text-align:justify;text-align-last:justify}
.card-text span:last-child{text-align-last:left}
.btn-more{left:54px;top:198px;width:93px;height:27px;border-radius:8px;background:linear-gradient(var(--orange-light),var(--orange-dark));border:1px solid #c8700c;color:#fff;font-size:16px;text-align:center;line-height:25px;box-shadow:0 2px 2px rgba(0,0,0,.2)}
.panel{background:var(--card);border:1px solid #e2e0df;border-radius:6px;box-shadow:0 2px 3px rgba(0,0,0,.15)}
.welcome{left:118px;top:798px;width:502px;height:298px}
.welcome h1{position:absolute;left:18px;top:24px;font-weight:400;font-size:20px;color:var(--orange)}
.welcome hr{position:absolute;left:18px;top:53px;width:461px;border:0;border-top:1px solid #ccc}
.welcome .body{position:absolute;left:19px;top:59px;width:461px;font-size:13.3px;line-height:20.3px;text-align:justify}
.welcome h2{font-weight:500;font-size:13.3px;color:var(--orange)}
.login{left:647px;top:797px;width:211px;height:299px;overflow:hidden}
.tab{left:36px;width:145px;height:58px;color:#fff;font-size:15px;text-align:center}
.tab svg{position:absolute;left:0;top:0}
.tab span{position:relative;display:block}
.field{left:19px;width:171px;height:30px;border:1px solid #e4e2e1;border-radius:6px;background:#f6f5f5;font-size:11.5px;color:#444;padding:7px 7px;box-shadow:inset 0 1px 2px rgba(0,0,0,.06)}
.btn-login{left:66px;top:159px;width:80px;height:31px;background:var(--orange);color:#fff;font-size:12.5px;text-align:center;line-height:31px;border-radius:2px}
.member{left:0;width:211px;top:212px;text-align:center;font-size:11.5px;color:#444}
.footer{left:0;top:1124px;width:976px;height:76px;background:linear-gradient(var(--footer-top),var(--footer-bottom))}
.copy{left:0;width:1008px;top:23px;text-align:center;font-size:11.5px;line-height:15px;color:#eee}
.ribbon{top:-2px;width:38px}
</style>
</head>
<body>
<div class="abs logo">Logo Here</div>

<nav class="abs nav">
  <a class="active" style="width:128px">Home</a>
  <a style="width:148px">About Us</a>
  <a style="width:143px">Find Job</a>
  <a style="width:169px">Register Here</a>
  <a style="width:160px">Contact Us</a>
</nav>

<div class="abs slider-band"></div>
<div class="abs slide-shadow"></div>
<div class="abs slide-frame">
  <div class="abs slide-photo" role="img" aria-label="Photo of engineers in hard hats reviewing plans together"></div>
</div>
<div class="abs dots"><span></span><span></span><span></span></div>

<section class="abs card" style="left:122px">
  <div class="abs card-head">About Us</div>
  <p class="card-text"><span>We need a design for the</span><span>login page, about page, and</span><span>inner pages of a recruitment</span><span>site for an oil and gas</span><span>company. Design should be</span><span>modern, sleek, professional.</span></p>
  <div class="abs btn-more">More</div>
</section>
<section class="abs card" style="left:390px">
  <div class="abs card-head">Environment</div>
  <p class="card-text"><span>We need a design for the</span><span>login page, about page, and</span><span>inner pages of a recruitment</span><span>site for an oil and gas</span><span>company. Design should be</span><span>modern, sleek, professional.</span></p>
  <div class="abs btn-more">More</div>
</section>
<section class="abs card" style="left:651px">
  <div class="abs card-head">Job Seeker</div>
  <p class="card-text"><span>We need a design for the</span><span>login page, about page, and</span><span>inner pages of a recruitment</span><span>site for an oil and gas</span><span>company. Design should be</span><span>modern, sleek, professional.</span></p>
  <div class="abs btn-more">More</div>
</section>

<section class="abs panel welcome">
  <h1>Welcome to our site</h1>
  <hr>
  <div class="body">
    <p>We need a design for the login page, about page, and inner pages of a recruitment site for an oil and gas company. Design should be modern, sleek, professional. We need a design for the login page, about page, and inner pages of a recruitment site for an oil and gas company. Design should be modern, sleek, professional. We need a design for the login page, about page, and inner pages of a recruitment site for an oil and gas company. Design should be modern, sleek, professional.</p>
    <h2>Our Great Work Environment:</h2>
    <p>We need a design for the login page, about page, and inner pages of a recruitment site for an oil and gas company. Design should be modern, sleek, professional.</p>
  </div>
</section>

<section class="abs panel login">
  <div class="abs tab" style="top:-2px">
    <svg width="145" height="58" viewBox="0 0 145 58">
      <defs><linearGradient id="tabTop" x1="0" y1="0" x2="0" y2="1"><stop offset="0" stop-color="#f2a623"/><stop offset="1" stop-color="#d5710a"/></linearGradient></defs>
      <path d="M0 0H145L124 50Q121 57 112 57H33Q24 57 21 50Z" fill="#e9e7e6"/>
      <path d="M8 0H137L119 45Q116 52 108 52H37Q29 52 26 45Z" fill="url(#tabTop)"/>
    </svg>
    <span style="top:24px">Login Now</span>
  </div>
  <div class="abs field" style="top:76px">User Name</div>
  <div class="abs field" style="top:119px">Password</div>
  <div class="abs btn-login">Login</div>
  <div class="abs member">Not a Member?</div>
  <div class="abs tab" style="left:20px;width:179px;top:242px">
    <svg width="179" height="58" viewBox="0 0 179 58">
      <defs><linearGradient id="tabBottom" x1="0" y1="0" x2="0" y2="1"><stop offset="0" stop-color="#f7b53a"/><stop offset="1" stop-color="#d5710a"/></linearGradient></defs>
      <path d="M0 58L22 8Q26 0 36 0H143Q153 0 157 8L179 58Z" fill="#e9e7e6"/>
      <path d="M10 58L30 14Q34 6 44 6H135Q145 6 149 14L169 58Z" fill="url(#tabBottom)"/>
    </svg>
    <span style="top:22px">Register Here</span>
  </div>
</section>

<footer class="abs footer">
  <div class="abs copy">Copyright @ 2012, All rights reserved.<br>Terms &amp; Privacy Policy</div>
  <svg class="abs ribbon" style="left:720px" width="38" height="63" viewBox="0 0 38 63" role="img" aria-label="Social link">
    <path d="M0 0H38V63L19 53L0 63Z" fill="#e08412"/><path d="M3 0H35V57L19 49L3 57Z" fill="#c96f0a"/>
  </svg>
  <svg class="abs ribbon" style="left:763px" width="38" height="63" viewBox="0 0 38 63" role="img" aria-label="Social link">
    <path d="M0 0H38V63L19 53L0 63Z" fill="#e08412"/><path d="M3 0H35V57L19 49L3 57Z" fill="#c96f0a"/>
  </svg>
</footer>
</body>
</html>
```